Kestrel Facilities Business Card Design

We would now like to design business cards with the new Kestrel Facilities logo

Target Market(s)

Professional

Industry/Entity Type

Professional services

Contact Information for Business Card

Employee name, title, phone number, email address, corporate office address and logo.

Font styles to use
Sans Serif

Colors
0054AA
0677BA
7BADD7
CADEEF
E8F1F8

Requirements
Must have
• My logo
Should not have
• any other pictures or images besides my logo

```html
<!DOCTYPE html>
<html lang="en">
<head>
<meta charset="utf-8">
<title>Kestrel Facilities Business Card</title>
<link href="https://fonts.googleapis.com/css2?family=Open+Sans:wght@400;700&display=swap" rel="stylesheet">
<style>
  :root {
    --blue-deep: #0054AA;
    --blue-mid: #0677BA;
    --blue-card: #2f6fc4;
    --blue-light: #7BADD7;
    --blue-pale: #CADEEF;
    --blue-mist: #E8F1F8;
    --paper: #ffffff;
    --backdrop: #d6d5d3;
    --ink-grey: #6b6b6b;
  }
  * { margin: 0; padding: 0; box-sizing: border-box; }
  html, body {
    width: 1200px; height: 801px; overflow: hidden;
    background: var(--backdrop);
    font-family: "Open Sans", Arial, sans-serif;
  }
  .stage {
    width: 1200px; height: 801px;
    display: flex; align-items: center; justify-content: center; gap: 48px;
  }
  .card {
    width: 520px; height: 297px; position: relative; overflow: hidden;
    box-shadow: 0 10px 24px rgba(0,0,0,0.18);
  }
  .card-front {
    background: var(--paper);
    border-bottom: 3px solid var(--blue-card);
    display: flex; align-items: center;
  }
  .identity {
    width: 260px; padding-right: 22px; text-align: right;
  }
  .identity-name {
    color: var(--blue-card); font-weight: 700; font-size: 22px; letter-spacing: 0.5px;
  }
  .identity-title {
    color: var(--ink-grey); font-size: 14px; margin-top: 2px;
  }
  .divider {
    width: 1px; height: 118px; background: var(--blue-card);
  }
  .contact {
    padding-left: 22px; color: var(--ink-grey); font-size: 14px; line-height: 22px;
  }
  .contact-row { display: flex; align-items: center; gap: 6px; }
  .contact-row svg { width: 11px; height: 11px; fill: var(--blue-card); flex: none; }
  .card-back { background: var(--blue-card); }
  .pattern-field {
    position: absolute; inset: 0;
    background: linear-gradient(135deg, var(--blue-deep) 0%, var(--blue-card) 55%, #3f86cf 100%);
  }
  .brand-band {
    position: absolute; top: 96px; right: 0; width: 190px; height: 110px;
    background: #3a7cc9;
    display: flex; align-items: center; justify-content: center;
  }
  .brand-name {
    color: var(--paper); font-weight: 700; font-size: 17px; line-height: 20px;
    text-align: left; letter-spacing: 0.5px;
  }
</style>
</head>
<body>
<main class="stage">
  <section class="card card-front">
    <div class="identity">
      <h1 class="identity-name">DANIEL ARVENSON</h1>
      <p class="identity-title">CEO</p>
    </div>
    <div class="divider"></div>
    <div class="contact">
      <p>1450 Meridian Road</p>
      <p>Lakeview, MA 845</p>
      <p class="contact-row"><svg viewBox="0 0 12 12"><path d="M2.5 1 L4.5 1 L5.2 3.6 L4 4.6 Q5 7 7.4 8 L8.4 6.8 L11 7.5 L11 9.5 Q10 11 8 11 Q1 9 1 3 Q1 1.5 2.5 1Z"/></svg>555-214-3807</p>
      <p class="contact-row"><svg viewBox="0 0 12 12"><path d="M0 2 H12 V10 H0Z M0 2 L6 7 L12 2" stroke="#fff" stroke-width="1"/></svg>darvenson@kestrelfac.com</p>
      <p class="contact-row"><svg viewBox="0 0 12 12"><circle cx="6" cy="6" r="5.5"/></svg>www.kestrelfac.com</p>
    </div>
  </section>
  <section class="card card-back">
    <div class="pattern-field" role="img" aria-label="Repeating tonal pattern of the brand mark in blue shades"></div>
    <div class="brand-band">
      <p class="brand-name">KESTREL<br>FACILITIES</p>
    </div>
  </section>
</main>
</body>
</html>
```